Sales and Marketing company needs website page graphics

We are redesigning our website and need graphics for the top of our solution pages. Currently you’ll see that there is one photo graphic with a differing color screen for each section. We’re looking for photo graphic designs that will represent each unique solution section (lead generation, prospecting, hiring) and fit within the overall website design. We will add the section title text to the photo graphic. This will be a total of 3 graphics.

This is a link to the working website redesign: http://trevindale.com/brunexatemp/
The content on the working redesign page is correct and will give you a good sense for how we talk about each solution. You’ll notice that the redesign is text heavy. We’ll work on that next.

Our current website is: www.brunexa.com
You’ll get a good sense for our designs on our blog: http://www.brunexa.com/blog

As a company, our goal is to help our clients get more customers. We do that through consulting, training and outsourced lead generation. Key words that describe us: flexible, responsive, and fun. (Although you don’t see that in our current website, hopefully it comes through more on our blog – and then on our new website!)

We will need the graphic design in high resolution formats. We will own the copyright and intellectual property.

North American companies that earn $750K - $85M in annual revenue selling to other businesses. Most are in the computer technology industry.

Business Service

Sans Serif

• Fit the design of the website.
• If there are people in the graphics, I like to see diversity: Asian,Black, Latin, Caucasian, men and women.
• Be creative, not like every other graphic you see on a website. We are a woman owned business and Marisol is well known. We don't want to feel generic. Potentially be something we can use elements of for other graphics.
• We really want your expertise and this is our first project with Artvoyle .
• We will insert the solution section text, so there wouldn't be the text unless it's part of the graphic design.

```html
<!DOCTYPE html>
<html lang="en">
<head>
<meta charset="utf-8">
<title>Brunexa Group – Lead Generation</title>
<link rel="stylesheet" href="https://fonts.googleapis.com/css2?family=Lato:wght@400;700&display=swap">
<style>
  :root{
    --purple:#5c2e88;
    --purple-text:#6a3a98;
    --green:#8cc63f;
    --ink:#3d3d3d;
    --grey:#9a9a9a;
    --grey-dark:#7d7d7d;
    --page:#ffffff;
    --bg:#f1f3f5;
  }
  *{box-sizing:border-box;margin:0;padding:0}
  html,body{width:1200px;height:757px;overflow:hidden;background:var(--bg)}
  body{font-family:"Lato",Arial,sans-serif;color:var(--ink)}
  .page{width:1200px;height:757px;background:var(--page);display:flex;flex-direction:column}
  .site-header{height:92px;display:flex;align-items:center;padding:0 48px 0 110px;position:relative}
  .brand{display:flex;align-items:center;gap:10px;font-size:40px;font-weight:700;color:var(--purple);letter-spacing:-1px}
  .brand-dot{width:14px;height:14px;border-radius:50%;background:var(--green)}
  .speak-link{position:absolute;left:720px;top:50px;font-size:12px;font-weight:700;color:var(--purple);letter-spacing:.5px}
  .phone{position:absolute;right:40px;top:14px;font-size:20px;font-weight:700;color:var(--purple)}
  .main-nav{height:30px;background:var(--purple);display:flex;justify-content:flex-end;padding-right:30px}
  .main-nav a{color:#fff;text-decoration:none;font-size:10.5px;font-weight:700;letter-spacing:.4px;padding:0 11px;line-height:30px}
  .main-nav a.is-active{background:var(--green)}
  .hero{height:312px;background:radial-gradient(ellipse at 72% 55%,#f3f0a0 0%,#a9b53a 10%,#4f5d1c 30%,#1d2410 58%,#0d100a 100%);border-bottom:3px solid var(--green)}
  .content{flex:1;display:flex;padding:26px 70px 0 110px;gap:40px}
  .system-diagram{width:300px;flex:none}
  .intro{flex:1;font-size:12.5px;line-height:1.55}
  .intro h1{font-size:30px;font-weight:400;color:var(--purple-text);margin-bottom:10px}
  .intro p{margin-bottom:9px}
  .intro mark{background:#3b7ed6;color:#fff;padding:0 2px}
  .intro ul{margin:0 0 9px 18px}
</style>
</head>
<body>
<div class="page">
  <header class="site-header">
    <div class="brand"><span>Brunexa group</span><span class="brand-dot"></span></div>
    <a class="speak-link">HIRE MARISOL TO SPEAK</a>
    <div class="phone">+1 555 014 2290</div>
  </header>
  <nav class="main-nav">
    <a>ABOUT</a><a>WHAT WE DO</a><a class="is-active">LEAD GENERATION</a><a>PROSPECTING</a><a>HIRING &amp; ONBOARDING</a><a>RESOURCES</a><a>EVENTS</a><a>BLOG</a><a>CONTACT</a>
  </nav>
  <div class="hero" role="img" aria-label="Dark green photo graphic: business people standing on a glowing world map with a globe held in an open hand"></div>
  <section class="content">
    <svg class="system-diagram" viewBox="0 0 300 230" aria-label="Revenue Generating System diagram">
      <circle cx="150" cy="130" r="88" fill="#ffffff" stroke="var(--grey)" stroke-width="6"/>
      <text x="150" y="128" text-anchor="middle" font-family="Lato,sans-serif" font-size="17" fill="var(--grey-dark)">Revenue</text>
      <text x="150" y="147" text-anchor="middle" font-family="Lato,sans-serif" font-size="17" fill="var(--grey-dark)">Generating</text>
      <text x="150" y="166" text-anchor="middle" font-family="Lato,sans-serif" font-size="17" fill="var(--grey-dark)">System</text>
      <circle cx="150" cy="46" r="42" fill="var(--green)" stroke="#fff" stroke-width="4"/>
      <text x="150" y="40" text-anchor="middle" font-family="Lato,sans-serif" font-size="8" font-weight="700" fill="#fff">LEAD</text>
      <text x="150" y="50" text-anchor="middle" font-family="Lato,sans-serif" font-size="8" font-weight="700" fill="#fff">GENERATION</text>
      <circle cx="62" cy="180" r="42" fill="var(--grey)" stroke="#fff" stroke-width="4"/>
      <text x="62" y="183" text-anchor="middle" font-family="Lato,sans-serif" font-size="8" font-weight="700" fill="#fff">PROSPECTING</text>
      <circle cx="238" cy="180" r="42" fill="var(--grey)" stroke="#fff" stroke-width="4"/>
      <text x="238" y="178" text-anchor="middle" font-family="Lato,sans-serif" font-size="8" font-weight="700" fill="#fff">HIRING &amp;</text>
      <text x="238" y="188" text-anchor="middle" font-family="Lato,sans-serif" font-size="8" font-weight="700" fill="#fff">ONBOARDING</text>
    </svg>
    <div class="intro">
      <h1>The Brunexa Group Approach to Lead Generation</h1>
      <p>The Brunexa Group lead generation philosophy is centered on <mark>consistency</mark>. Successful lead generation includes a linking of multiple activities together that keeps you in front of your target market without annoying them.</p>
      <p>We believe the most effective lead generation:</p>
      <ul>
        <li>engages a variety of lead generation activities</li>
        <li>targets specific micro-segments of your client base</li>
        <li>employs a focused message on the business issues your prospects are experiencing</li>
      </ul>
      <p>Most importantly, we believe these activities have to fit your company's resources and culture just as much as they have to fit the micro-segment you are targeting.</p>
      <p>The Brunexa Group process to lead generation combines a mix of outbound and inbound lead generation and sales activities into one integrated communication strategy.</p>
    </div>
  </section>
</div>
</body>
</html>
```